Tandem Hearth Works Pty Ltd

We need business cards for a company based in Perth, we install, service and maintain fire equipment.
On the front we want a great design with our logo and a small spot for our full company name, general company email address and office number. On the back we need space for our name, title, mobile number and email address on the back.

Target Market(s)

Facility managers and commercial/industrial building owners/occupiers.

Contact Information for Business Card

Font styles to use
Sans Serif

Requirements
Must have
• Please only submit 5 of your best samples.
Darker tones are preferred.
Nice to have
• We want to use, black, red and grey. Keep it modern and clean.
I've attached the company logo and a sample of a boarder we use on our emergency plans.
Should not have
• No preference. Let the designer choose.

```html
<!DOCTYPE html>
<html lang="en">
<head>
<meta charset="utf-8">
<title>Tandem Hearth Works – Business Cards</title>
<link rel="stylesheet" href="https://fonts.googleapis.com/css2?family=Arimo:wght@400;700&display=swap">
<style>
  :root {
    --bg: #2b2b2d;
    --card: #1c1c1e;
    --card-edge: #232325;
    --red: #ec1c24;
    --grey: #cfcfcf;
    --grey-dim: #8a8a8c;
    --rule: #4a4a4c;
  }
  * { box-sizing: border-box; margin: 0; padding: 0; }
  html, body {
    width: 1200px; height: 1108px; overflow: hidden;
    background: var(--bg);
    font-family: "Arimo", Arial, sans-serif;
  }
  .sheet {
    position: relative; width: 1200px; height: 1108px;
    display: flex; justify-content: center; align-items: center; gap: 60px;
  }
  .card {
    width: 420px; height: 660px;
    background: var(--card);
    border-radius: 22px;
    box-shadow: 0 18px 40px rgba(0,0,0,.45);
    position: relative; overflow: hidden;
  }
  .card--front {
    display: flex; flex-direction: column; align-items: center;
    text-align: center; padding: 110px 40px 40px;
  }
  .wordmark {
    font-weight: 700; color: var(--red);
    font-size: 120px; line-height: 1; letter-spacing: -2px;
  }
  .person { margin-top: 70px; }
  .person__name {
    color: var(--red); font-weight: 700; font-size: 24px;
    text-transform: uppercase; letter-spacing: .5px;
  }
  .person__title { color: var(--grey); font-size: 20px; margin-top: 4px; }
  .rule { width: 150px; height: 1px; background: var(--rule); margin: 16px auto; }
  .contact { color: var(--grey); font-size: 20px; line-height: 1.35; }
  .company {
    color: var(--red); font-weight: 700; font-size: 24px;
    text-transform: uppercase; line-height: 1.15;
  }
  .office-phone {
    color: var(--grey); font-weight: 700; font-size: 30px; margin-top: 12px;
  }
  .web { color: var(--grey); font-size: 18px; margin-top: 18px; }
  .web .accent { color: var(--red); }
  .card--back { background: var(--card); }
  .back-texture {
    position: absolute; inset: 0 0 35% 0;
    background: linear-gradient(160deg, #262628 0%, #1f1f21 100%);
  }
  .card--back .wordmark--small {
    position: absolute; right: 70px; bottom: 170px;
    font-size: 54px; font-weight: 700; color: var(--red); line-height: 1;
  }
</style>
</head>
<body>
  <main class="sheet">
    <section class="card card--front">
      <div class="wordmark">THW</div>
      <div class="person">
        <p class="person__name">Marcus Hale</p>
        <p class="person__title">Managing Director</p>
      </div>
      <div class="rule"></div>
      <div class="contact">
        <p>555.0142.0142</p>
        <p>name@thw.com</p>
      </div>
      <div class="rule"></div>
      <p class="company">Tandem Hearth Works<br>Pty Ltd</p>
      <p class="office-phone">555.0190.0190</p>
      <p class="web">info@thw.com | www.<span class="accent">thw</span>.com</p>
    </section>
    <section class="card card--back">
      <div class="back-texture" role="img" aria-label="Faint tone-on-tone repeated brand pattern"></div>
      <div class="wordmark--small">THW</div>
    </section>
  </main>
</body>
</html>
```